Stylish Business Cards Wanted

- DOUBLE SIDED Design Required -

High end, edgy cards for a corporate and personal stylist. Must include logo,
Name: Belinda Harwick
Title: Director and Stylist
telephone : +61 8 7142 5809
email: belinda@theloombriefing.example
website: theloombriefing.example
Tag: Corporate Workwear & Uniform Specialist | Personal Stylist
Would like nice icons for telephone, email, website

Target Market(s)

Businesses wanting stylish uniforms, people wanting stylish wardrobes

Industry/Entity Type

Corporate Workwear Stylist

Contact Information for Business Card

I would like black, white and gold foiling incorporated in the design - possibly a touch of the other colours on my branding guide attached Name: Belinda Harwick Title: Director and Stylist telephone : +61 8 7142 5809 email: belinda@theloombriefing.example website: theloombriefing.example Tag: Corporate Workwear & Uniform Specialist | Personal Stylist Would like nice icons for telephone, email, website

Font styles to use
Other font styles liked:
• Raleway

Colors

Designer to choose colors to be used in the design.

Requirements
Must have
• Gold foil accents

```html
<!DOCTYPE html>
<html lang="en">
<head>
<meta charset="utf-8">
<title>The Loom Briefing – Business Cards</title>
<link href="https://fonts.googleapis.com/css2?family=Open+Sans:wght@400;600;700&display=swap" rel="stylesheet">
<style>
  :root {
    --backdrop: #3b3b3b;
    --card: #1c1c1c;
    --gold: #d4a843;
    --white: #f4f4f4;
    --deboss: #3a3a3a;
  }
  * { box-sizing: border-box; margin: 0; padding: 0; }
  html, body { width: 1200px; height: 801px; overflow: hidden; }
  body {
    background: var(--backdrop);
    font-family: "Open Sans", Arial, sans-serif;
    display: flex;
    align-items: center;
    justify-content: center;
    gap: 40px;
  }
  .card {
    position: relative;
    width: 540px;
    height: 309px;
    background: var(--card);
    border-bottom: 2px solid var(--gold);
    border-right: 2px solid var(--gold);
    box-shadow: 0 0 0 1px rgba(212,168,67,0.35);
  }
  /* Front */
  .front .brand {
    position: absolute;
    left: 40px;
    top: 96px;
    width: 200px;
    color: var(--white);
    font-size: 30px;
    font-weight: 600;
    line-height: 1.15;
  }
  .front .divider {
    position: absolute;
    left: 262px;
    top: 46px;
    width: 1px;
    height: 120px;
    background: var(--gold);
  }
  .front .details {
    position: absolute;
    left: 284px;
    top: 48px;
    color: var(--white);
  }
  .details .name {
    color: var(--gold);
    font-weight: 700;
    font-size: 17px;
    letter-spacing: 0.5px;
    text-transform: uppercase;
  }
  .details .title {
    font-size: 12.5px;
    margin: 2px 0 16px;
  }
  .contact-list { list-style: none; font-size: 11.5px; }
  .contact-list li {
    display: flex;
    align-items: center;
    gap: 7px;
    margin-bottom: 5px;
  }
  .contact-list svg { width: 11px; height: 11px; fill: var(--gold); flex: none; }
  .front .tagline {
    position: absolute;
    left: 40px;
    right: 30px;
    bottom: 36px;
    color: var(--white);
    font-size: 12.5px;
  }
  .tagline .dot { color: var(--gold); margin: 0 8px; }
  /* Back */
  .back .brand-deboss {
    position: absolute;
    inset: 0;
    display: flex;
    align-items: center;
    justify-content: center;
    color: var(--deboss);
    font-size: 44px;
    font-weight: 600;
  }
</style>
</head>
<body>
  <section class="card front" aria-label="Business card front">
    <div class="brand">The Loom Briefing</div>
    <div class="divider"></div>
    <div class="details">
      <p class="name">Belinda Harwick</p>
      <p class="title">Director and Stylist</p>
      <ul class="contact-list">
        <li>
          <svg viewBox="0 0 12 12" aria-hidden="true"><path d="M2.4 0.6 4.3 2.5 3.3 4.2c.7 1.6 2 2.9 3.6 3.6l1.7-1 1.9 1.9-1.3 1.9C4.9 10.3 1.4 6.9.5 2z"/></svg>
          +61 8 7142 5809
        </li>
        <li>
          <svg viewBox="0 0 12 12" aria-hidden="true"><path d="M0 2h12v8H0z M0.8 2.6 6 6.6l5.2-4" stroke="#1c1c1c" stroke-width="1"/></svg>
          belinda@theloombriefing.example
        </li>
        <li>
          <svg viewBox="0 0 12 12" aria-hidden="true"><circle cx="6" cy="6" r="5.5"/><path d="M0.5 6h11M6 .5c-3 3-3 8 0 11M6 .5c3 3 3 8 0 11" stroke="#1c1c1c" stroke-width="0.9" fill="none"/></svg>
          theloombriefing.example
        </li>
      </ul>
    </div>
    <p class="tagline">Corporate Workwear &amp; Uniform Specialist<span class="dot">•</span>Personal Stylist</p>
  </section>

  <section class="card back" aria-label="Business card back">
    <div class="brand-deboss">The Loom Briefing</div>
  </section>
</body>
</html>
```